Venture Capital firm needs modern business cards

We are a Venture Capital firm within financial services/Asset management. The industry generally has basic business cards with black, blue and maybe green/yellow design elements.
Our firm has a four-colour swoosh logo. We are based in London and want to stand out, just a little bit!, from the crowd. Our company is called LORV Investments and the 'C' stands for collaboration thus using makerswarm is a natural portal for our business card design competition. Our logo came via makerswarm too!
We use 'Venture Partner in Asset Management' as our tagline and this is Trademark registered. We operate in a conservative industry and we should not overstep our mark. The logo is colorful as it is and therefore the rest of the design should not be too fanciful.
The objective is twofold: make our logo element stick and memorable with our audience, whilst representing a conservative yet young image.
Updates
The Business Card obviously needs a field for Name, Surname, Job Title, Adress fields: Street, City, Postcode, Country, telefone and cell number, website address, etc.
We have uploaded the ai file. We trust that these are OK. If not, please advise.
Reason: We have have been busy with a client engagement. We will set the project as Guaranteed in return for the troubles we cause. Apologies for the confusion.
Thank you all for these great and creative design suggestions. The team is very happy with a number of your ideas! We will be in touch tomorrow to give individual feedback before the project closes on Friday. We look forward to working with some of you to narrow down your creations. Thank you, LORV Investments team.
All,
Target Market(s)
Financial Services Professionals, Investors, Media, 35-70 years, mainly male, well educated
Industry/Entity Type
Conservative
Requirements
Must have
- We must make use of our logo and potential tagline 'Venture Partner in Asset Management' as we are establishing a new Brand and new company in the market.
We can use 'LORV', 'LORV Investments', and 'LORV Investments'+tagline 'Venture Partner in Asset Management' or simply the four-colour swoosh plus the name of the company as part of the text. (see files)
All design elements are available in black or grey-scale if required. (grey scale swoosh attached).
Due to regulation we must have the following wording on the card in small print 'LORV Investments is an Appointed Representative of Bramwell Holdings Partnership Limited, which is authorised by the Monetary Oversight Board'.
Nice to have
- We would consider designs that make use of different printing techniques such embossing/debossing, UV spot etc.
We attach our colour palette in the files section for your reference.
Should not have
- The font we use for our company name is 'EXO' so do not use a font style that clashes with the corporate fonts, please.
Do not use other design elements than the ones we provide in the file library as part of this project.

```html
<!DOCTYPE html>
<html lang="en">
<head>
<meta charset="utf-8">
<title>LORV Investments – Business Card</title>
<link rel="stylesheet" href="https://fonts.googleapis.com/css2?family=Open+Sans:wght@400;600&display=swap">
<style>
  :root {
    --backdrop: #e9e6e3;
    --card: #ffffff;
    --card-back: #f4f4f4;
    --ink: #3a3a3a;
    --ink-soft: #6d6d6d;
    --ink-faint: #9a9a9a;
    --accent: #2a9fd8;
    --rule: #d6d6d6;
    --mark: #dcdcdc;
  }
  * { box-sizing: border-box; margin: 0; padding: 0; }
  html, body { width: 1200px; height: 878px; overflow: hidden; }
  body {
    background: var(--backdrop);
    font-family: "Open Sans", Arial, sans-serif;
    color: var(--ink);
    position: relative;
  }
  .card {
    position: absolute;
    width: 520px;
    height: 298px;
    border-radius: 14px;
    box-shadow: 0 6px 18px rgba(0,0,0,0.18);
  }
  /* Front */
  .card-front {
    left: 50px; top: 290px;
    background: var(--card);
    display: flex; align-items: center;
    padding-left: 64px; gap: 44px;
  }
  .front-dot {
    width: 130px; height: 130px; border-radius: 50%;
    background: var(--mark);
  }
  .front-name {
    font-size: 40px; font-weight: 600; color: var(--ink);
    letter-spacing: 0.5px; line-height: 1.1;
  }
  /* Back */
  .card-back {
    left: 630px; top: 290px;
    background: var(--card-back);
  }
  .divider {
    position: absolute; left: 290px; top: 20px; bottom: 20px;
    width: 1px; background: var(--rule);
  }
  .brand {
    position: absolute; left: 36px; top: 100px;
  }
  .brand-row { display: flex; align-items: center; gap: 10px; }
  .brand-dot { width: 30px; height: 30px; border-radius: 50%; background: var(--mark); }
  .brand-name { font-size: 40px; font-weight: 600; color: var(--ink); line-height: 1; }
  .tagline {
    margin-left: 40px; margin-top: 4px;
    font-size: 7.5px; color: var(--ink-soft);
    border-top: 1px solid var(--ink-soft); padding-top: 2px; width: 190px;
  }
  .small-print {
    position: absolute; left: 30px; width: 240px; top: 226px;
    font-size: 7px; font-style: italic; line-height: 1.35;
    color: var(--ink-faint); text-align: center;
  }
  .person {
    position: absolute; right: 34px; top: 46px; text-align: right;
  }
  .person-name { font-size: 20px; color: var(--ink); line-height: 1.1; }
  .person-title { font-size: 15px; font-weight: 600; color: var(--accent); line-height: 1.1; }
  .contacts {
    position: absolute; right: 34px; top: 166px;
    list-style: none; text-align: right;
  }
  .contacts li {
    display: flex; justify-content: flex-end; align-items: center; gap: 8px;
    font-size: 13px; color: var(--ink); line-height: 19px;
  }
  .contacts svg { width: 10px; height: 10px; fill: var(--ink-soft); flex: none; }
  .contacts .gap { margin-bottom: 4px; }
</style>
</head>
<body>
  <section class="card card-front" aria-label="Card front">
    <div class="front-dot"></div>
    <div class="front-name">LORV Investments</div>
  </section>

  <section class="card card-back" aria-label="Card back">
    <div class="brand">
      <div class="brand-row">
        <div class="brand-dot"></div>
        <div class="brand-name">LORV</div>
      </div>
      <div class="tagline">Venture Partner in Asset Management</div>
    </div>
    <p class="small-print">LORV Investments is an Appointed Representative of Bramwell Holdings Partnership Limited, which is authorised by the Monetary Oversight Board</p>

    <div class="divider"></div>

    <div class="person">
      <div class="person-name">Daniel Hart</div>
      <div class="person-title">manager</div>
    </div>

    <ul class="contacts">
      <li>Adress line 1
        <svg viewBox="0 0 10 10"><path d="M5 0a3.5 3.5 0 0 0-3.5 3.5C1.5 6 5 10 5 10s3.5-4 3.5-6.5A3.5 3.5 0 0 0 5 0zm0 5a1.4 1.4 0 1 1 0-2.8A1.4 1.4 0 0 1 5 5z"/></svg>
      </li>
      <li class="gap">Adress line 2 <svg viewBox="0 0 10 10"></svg></li>
      <li>+380 11 222 333
        <svg viewBox="0 0 10 10"><path d="M2 0l2 2.5-1.2 1.3a6 6 0 0 0 3.4 3.4L7.5 6 10 8l-1.3 1.7C4.5 10 0 5.5.3 1.3z"/></svg>
      </li>
      <li>+380 11 222 334
        <svg viewBox="0 0 10 10"><path d="M3 0h4a1 1 0 0 1 1 1v8a1 1 0 0 1-1 1H3a1 1 0 0 1-1-1V1a1 1 0 0 1 1-1zm0 1.5v6h4v-6z"/></svg>
      </li>
      <li>daniel.hart@lorv.com
        <svg viewBox="0 0 10 10"><path d="M0 2h10v6H0zm1 1l4 3 4-3z" fill-rule="evenodd"/></svg>
      </li>
      <li>www.lorv.com
        <svg viewBox="0 0 10 10"><circle cx="5" cy="5" r="4.5" fill="none" stroke="#6d6d6d" stroke-width="1"/><path d="M0.5 5h9M5 0.5c-2.5 3-2.5 6 0 9M5 0.5c2.5 3 2.5 6 0 9" fill="none" stroke="#6d6d6d" stroke-width="0.8"/></svg>
      </li>
    </ul>
  </section>
</body>
</html>
```